New Business Card Design Project

Use the flyer uploaded and website www.brightoakbuilders.com for inspiration.
List Our Services on Backside of business cards
Marcus Delling
Harborline Builders Inc.
Licensed General Contractors
858-471-6093

Contact Information for Business Card

Use the flyer uploaded and website www.brightoakbuilders.com for inspiration. List Our Services on Backside of business cards Marcus Delling Harborline Builders Inc. Licensed General Contractors 858-471-6093

```html
<!DOCTYPE html>
<html lang="en">
<head>
<meta charset="utf-8">
<title>Harborline Builders Business Cards</title>
<link href="https://fonts.googleapis.com/css2?family=Montserrat:wght@400;500;700;800&display=swap" rel="stylesheet">
<style>
  :root {
    --backdrop: #3b3b3b;
    --card: #141414;
    --ink: #ffffff;
    --ink-soft: #e6e6e6;
  }
  * { margin: 0; padding: 0; box-sizing: border-box; }
  html, body { width: 1200px; height: 998px; overflow: hidden; }
  body {
    background: var(--backdrop);
    font-family: "Montserrat", sans-serif;
    color: var(--ink);
    display: flex;
    flex-direction: column;
    align-items: center;
    justify-content: center;
    gap: 44px;
  }
  .card {
    width: 770px;
    height: 440px;
    background: var(--card);
    position: relative;
    overflow: hidden;
    box-shadow: 0 10px 30px rgba(0,0,0,.45);
  }
  .brand {
    position: absolute;
    font-weight: 500;
    letter-spacing: 4px;
    text-transform: uppercase;
    color: var(--ink);
    display: flex;
    align-items: center;
    gap: 14px;
  }
  .brand-square {
    width: 18px; height: 18px;
    border: 2px solid var(--ink);
  }

  /* Back: services */
  .card-back .brand { top: 110px; left: 0; right: 0; justify-content: center; font-size: 30px; }
  .services-heading {
    position: absolute;
    top: 205px; left: 48px; right: 48px;
    display: flex; align-items: center; gap: 18px;
    font-weight: 800; font-size: 22px; letter-spacing: 1px;
  }
  .services-heading .rule { flex: 1; height: 2px; background: var(--ink); }
  .services-list {
    position: absolute;
    top: 262px; left: 60px; right: 40px;
    display: grid;
    grid-template-columns: 1.05fr 1fr;
    column-gap: 30px;
  }
  .services-list ul { list-style: none; }
  .services-list li {
    display: flex; align-items: center; gap: 10px;
    font-size: 19px; line-height: 33px; color: var(--ink-soft);
  }
  .tick { width: 18px; height: 18px; flex: none; }

  /* Front: contact */
  .card-front .brand { top: 90px; right: 60px; font-size: 28px; }
  .contact {
    position: absolute;
    left: 400px; top: 185px;
  }
  .contact-name { font-weight: 800; font-size: 42px; line-height: 1.1; }
  .contact-title { font-weight: 700; font-size: 21px; margin-top: 6px; }
  .contact-rule { width: 250px; height: 2px; background: var(--ink); margin: 18px 0 22px; }
  .contact-line {
    display: flex; align-items: center; gap: 16px;
    font-size: 22px; line-height: 44px; color: var(--ink-soft);
  }
  .contact-line svg { width: 24px; height: 24px; flex: none; }
</style>
</head>
<body>

  <section class="card card-back">
    <div class="brand"><span class="brand-square"></span>Harborline Builders</div>
    <h2 class="services-heading"><span class="rule"></span>OUR SERVICES<span class="rule"></span></h2>
    <div class="services-list">
      <ul>
        <li><svg class="tick" viewBox="0 0 18 18"><rect x="1" y="1" width="16" height="16" fill="none" stroke="#fff" stroke-width="2"/><path d="M4 9l3.5 3.5L14 5" fill="none" stroke="#fff" stroke-width="2.4"/></svg>Remodel: Kitchen &amp; Bath</li>
        <li><svg class="tick" viewBox="0 0 18 18"><rect x="1" y="1" width="16" height="16" fill="none" stroke="#fff" stroke-width="2"/><path d="M4 9l3.5 3.5L14 5" fill="none" stroke="#fff" stroke-width="2.4"/></svg>Painting: Interior &amp; Exterior</li>
        <li><svg class="tick" viewBox="0 0 18 18"><rect x="1" y="1" width="16" height="16" fill="none" stroke="#fff" stroke-width="2"/><path d="M4 9l3.5 3.5L14 5" fill="none" stroke="#fff" stroke-width="2.4"/></svg>Flooring: Carpet, Vinyl, Wood</li>
        <li><svg class="tick" viewBox="0 0 18 18"><rect x="1" y="1" width="16" height="16" fill="none" stroke="#fff" stroke-width="2"/><path d="M4 9l3.5 3.5L14 5" fill="none" stroke="#fff" stroke-width="2.4"/></svg>Window &amp; Door Replacement</li>
      </ul>
      <ul>
        <li><svg class="tick" viewBox="0 0 18 18"><rect x="1" y="1" width="16" height="16" fill="none" stroke="#fff" stroke-width="2"/><path d="M4 9l3.5 3.5L14 5" fill="none" stroke="#fff" stroke-width="2.4"/></svg>Plumbing: Repairs &amp; Upgrades</li>
        <li><svg class="tick" viewBox="0 0 18 18"><rect x="1" y="1" width="16" height="16" fill="none" stroke="#fff" stroke-width="2"/><path d="M4 9l3.5 3.5L14 5" fill="none" stroke="#fff" stroke-width="2.4"/></svg>Energy-Efficient Upgrades</li>
        <li><svg class="tick" viewBox="0 0 18 18"><rect x="1" y="1" width="16" height="16" fill="none" stroke="#fff" stroke-width="2"/><path d="M4 9l3.5 3.5L14 5" fill="none" stroke="#fff" stroke-width="2.4"/></svg>Deck &amp; Patio Construction</li>
      </ul>
    </div>
  </section>

  <section class="card card-front">
    <div class="brand"><span class="brand-square"></span>Harborline Builders</div>
    <div class="contact">
      <h1 class="contact-name">Marcus Delling</h1>
      <p class="contact-title">Licensed General Contractors</p>
      <div class="contact-rule"></div>
      <p class="contact-line">
        <svg viewBox="0 0 24 24"><path d="M6.6 10.8a15 15 0 0 0 6.6 6.6l2.2-2.2a1 1 0 0 1 1-.25 11.4 11.4 0 0 0 3.6.57 1 1 0 0 1 1 1V20a1 1 0 0 1-1 1A17 17 0 0 1 3 4a1 1 0 0 1 1-1h3.5a1 1 0 0 1 1 1c0 1.25.2 2.45.57 3.57a1 1 0 0 1-.25 1z" fill="#fff"/></svg>
        858-471-6093
      </p>
      <p class="contact-line">
        <svg viewBox="0 0 24 24" fill="none" stroke="#fff" stroke-width="2"><circle cx="12" cy="12" r="10"/><path d="M2 12h20M12 2c3 3 3 17 0 20M12 2c-3 3-3 17 0 20"/></svg>
        www.brightoakbuilders.com
      </p>
    </div>
  </section>

</body>
</html>
```